Buch-/eBook-Cover für Traumatherapeutin
Zielgruppe
Ich bin Traumatherapeutin und schreibe ein Buch zum Thema Trauma bearbeiten.
Meine Zielgruppe sucht Heilung, Genesung, Selbstliebe etc.
Aufgabenstellung
Buchcover
Bitte erstell mir ein modernes positives inspirierendes Buchcover mit dem
Titel: 'Morgenlicht NEU entdecken“
Untertitel: „Spüre den Mut der ganz in dir wohnt“
Dr. Mira Kessow
Ich hätte gerne ein modernes Buch, das entweder einen Bezug zum Thema Trauma hat oder aber einfach stylische Schriftzüge. Bin aber auch offen für andere Vorschläge.
Dunkelblau, weiß und türkis oder auch rosa mag ich ganz gerne. Wobei Dunkelblau, weiß und türkis meine Favoriten sind und mit rosa höchstens kleinere Akzente gesetzt werden sollten.
Das Buchcover soll modern sein und direkt ansprechen. Gerne eine originelle Lösung, oder etwas Besonderes, etwas das Tiefe ausdrückt, oder man mehrmals hinsehen muss um etwas zu erkennen oder etwas das mehr Interpretationsspielraum lässt.
Gerne auch viel weiß, zumindest heller und nicht zu dunkel. Stylish, aber nicht überfrachtet.
Schreib mich gerne an, wenn du Fragen hast.
Ich habe mal zwei Beispiel von Typolösungen angehängt, die ich ganz cool fände.
Ich freue mich auf deine Ideen :-)
Ganz liebe Grüße
Mira

```html
<!DOCTYPE html>
<html lang="de">
<head>
<meta charset="utf-8">
<title>Morgenlicht NEU entdecken – Dr. Mira Kessow</title>
<link rel="stylesheet" href="https://fonts.googleapis.com/css2?family=Roboto:wght@400;700;900&display=swap">
<style>
  :root {
    --backdrop: #acd8db;
    --paper: #fdf5f2;
    --navy: #5c6d8f;
    --navy-deep: #3e5c7a;
    --turquoise: #abd4d5;
    --rose: #e8a88d;
    --white: #ffffff;
  }
  * { margin: 0; padding: 0; box-sizing: border-box; }
  html, body {
    width: 1200px;
    height: 1199px;
    overflow: hidden;
    background: var(--backdrop);
    font-family: "Roboto", Arial, sans-serif;
  }
  .cover {
    position: absolute;
    left: 200px;
    top: 0;
    width: 800px;
    height: 1199px;
    background: var(--paper);
    overflow: hidden;
  }
  .author {
    position: absolute;
    top: 84px;
    left: 0;
    width: 100%;
    text-align: center;
    font-size: 38px;
    font-weight: 400;
    letter-spacing: 0.08em;
    color: var(--navy);
    padding-left: 14px;
  }
  .title {
    position: absolute;
    left: 0;
    top: 0;
    width: 800px;
    height: 520px;
  }
  .title .line { fill: var(--navy); font-family: "Roboto", Arial, sans-serif; font-weight: 700; }
  .title .highlight-box { fill: var(--rose); }
  .title .highlight-word { fill: var(--white); font-family: "Roboto", Arial, sans-serif; font-weight: 900; }
  .subtitle {
    position: absolute;
    top: 566px;
    left: 0;
    width: 100%;
    text-align: center;
    font-size: 29px;
    line-height: 41px;
    font-weight: 400;
    color: var(--rose);
  }
  .illustration {
    position: absolute;
    left: 119px;
    top: 723px;
    width: 560px;
    height: 476px;
  }
  .illustration .shape-left { fill: var(--navy); }
  .illustration .shape-right { fill: var(--turquoise); }
  .illustration .shape-overlap { fill: var(--navy-deep); }
</style>
</head>
<body>
  <main class="cover">
    <p class="author">DR. MIRA KESSOW</p>

    <svg class="title" viewBox="0 0 800 520" aria-label="Morgenlicht NEU entdecken">
      <text class="line" x="165" y="277" font-size="68" textLength="510" lengthAdjust="spacing">MORGENLICHT</text>
      <rect class="highlight-box" x="138" y="298" width="540" height="118"/>
      <text class="highlight-word" x="408" y="395" font-size="108" text-anchor="middle" letter-spacing="14">NEU</text>
      <text class="line" x="155" y="491" font-size="72" textLength="509" lengthAdjust="spacing">ENTDECKEN</text>
    </svg>

    <p class="subtitle">Spüre den Mut<br>der ganz in dir wohnt</p>

    <svg class="illustration" viewBox="0 0 560 476" role="img" aria-label="Illustration: zwei einander zugewandte Kopfsilhouetten in Dunkelblau und Türkis, mit einer verknoteten und einer gelösten Linie im Kopf">
      <defs>
        <path id="form-left" d="M20 476 V150 A150 150 0 0 1 320 150 V476 Z"/>
        <path id="form-right" d="M240 476 V150 A150 150 0 0 1 540 150 V476 Z"/>
        <clipPath id="clip-left"><use href="#form-left"/></clipPath>
      </defs>
      <use class="shape-left" href="#form-left"/>
      <use class="shape-right" href="#form-right"/>
      <use class="shape-overlap" href="#form-right" clip-path="url(#clip-left)"/>
    </svg>
  </main>
</body>
</html>
```